Powepoint template for an investment group

Need high end clear clean concise creative luxurious

Have royal clients
High end/billionaire investors

Using ross gold logo can be creative
Must habe page numbers
Logo preference header top right
Page number footer bottom right

The first page of the ppt maybe a big block of dark grey and veltro investment group written on the front page in rose gold

Target Market(s)

Investors at a high level

Requirements
Must have
• Luxury feel

```html
<!DOCTYPE html>
<html lang="en">
<head>
<meta charset="utf-8">
<title>Veltro Investment Group – Lorem Ipsum</title>
<link href="https://fonts.googleapis.com/css2?family=Montserrat:wght@400;500;800&family=Karla:wght@300;400&display=swap" rel="stylesheet">
<style>
  :root {
    --ink: #0d0d0d;
    --muted: #c4c4c4;
    --kicker: #222222;
    --brand-tone: #b89489;
    --band: #f1f1f1;
    --page-bg: #ffffff;
    --photo-light: #d9d9d9;
    --photo-mid: #8a8a8a;
    --photo-dark: #2b2b2b;
  }
  * { margin: 0; padding: 0; box-sizing: border-box; }
  html, body {
    width: 1200px;
    height: 675px;
    overflow: hidden;
    background: var(--page-bg);
  }
  .slide {
    position: relative;
    width: 1200px;
    height: 675px;
    overflow: hidden;
    background: var(--page-bg);
    font-family: "Montserrat", sans-serif;
  }
  .slide-art {
    position: absolute;
    left: 0;
    top: 0;
    width: 1200px;
    height: 675px;
  }
  .brand {
    position: absolute;
    top: 36px;
    right: 50px;
    display: flex;
    align-items: center;
    gap: 8px;
    color: var(--brand-tone);
    font-family: "Montserrat", sans-serif;
    font-weight: 500;
    font-size: 13px;
    letter-spacing: 0;
  }
  .brand-square {
    width: 10px;
    height: 10px;
    background: var(--brand-tone);
  }
  .content {
    position: absolute;
    left: 754px;
    top: 148px;
    width: 400px;
  }
  .kicker {
    font-size: 13px;
    font-weight: 400;
    letter-spacing: 3.4px;
    color: var(--kicker);
    text-transform: uppercase;
  }
  .headline {
    margin-top: 10px;
    font-size: 40px;
    font-weight: 800;
    line-height: 1.23;
    letter-spacing: 3px;
    color: var(--ink);
    text-transform: uppercase;
  }
  .body-copy {
    margin-top: 22px;
    font-family: "Karla", sans-serif;
    font-weight: 300;
    font-size: 14.4px;
    line-height: 23.75px;
    color: var(--muted);
    width: 365px;
  }
  .body-copy p + p { margin-top: 22px; }
  .page-number {
    position: absolute;
    right: 92px;
    bottom: 24px;
    font-family: "Karla", sans-serif;
    font-size: 13px;
    color: var(--muted);
  }
</style>
</head>
<body>
<main class="slide">
  <svg class="slide-art" viewBox="0 0 960 540" preserveAspectRatio="none">
    <defs>
      <linearGradient id="tower-tones" x1="0" y1="0" x2="1" y2="1">
        <stop offset="0" stop-color="#d9d9d9"/>
        <stop offset="0.45" stop-color="#8a8a8a"/>
        <stop offset="1" stop-color="#2b2b2b"/>
      </linearGradient>
      <clipPath id="prism-shape">
        <polygon points="0,0 438,0 212,410 0,48"/>
        <polygon points="452,0 545,0 258,490 224,418"/>
      </clipPath>
    </defs>
    <polygon class="accent-band" points="262,540 296,540 608,0 574,0" fill="#f1f1f1"/>
    <g role="img" aria-label="Black and white photograph of glass skyscrapers seen from below">
      <rect x="0" y="0" width="560" height="500" fill="url(#tower-tones)" clip-path="url(#prism-shape)"/>
    </g>
  </svg>

  <header class="brand">
    <span class="brand-square"></span>
    <span class="brand-name">Veltro Investment Group</span>
  </header>

  <section class="content">
    <p class="kicker">Lorem Ipsum</p>
    <h1 class="headline">Lorem ipsum<br>is simply<br>dummy</h1>
    <div class="body-copy">
      <p>Lorem Ipsum is simply dummy text of the printing and typesetting industry. Lorem Ipsum has been the industry's standard dummy text ever since the 1500s, when an unknown printer took a galley of type and scrambled it to make a type specimen book.</p>
      <p>Lorem Ipsum is simply dummy text of the printing and typesetting industry.</p>
    </div>
  </section>

  <footer class="page-number">3</footer>
</main>
</body>
</html>
```